Private Investment Firm Needs PowerPoint Presentation Template

Design PowerPoint template, take Pinebrook-submitted rough presentation draft, and drop it into new template. See attached Project Brief file for more detail.
Updates

Some decent designs have been submitted but they seem to lack the understanding of our target markets. I am hopeful that more time and feedback will result in better results.

Target Market(s)

Private company owners and intermediaries.

Font styles to use
Serif

Colors
3176b5

Requirements
Must have
• See attached Project Brief.
Nice to have
Should not have
• No B2C fluff--this is a B2B project.

```html
<!DOCTYPE html>
<html lang="en">
<head>
<meta charset="utf-8">
<title>When Is a Non-Control Transaction Appropriate?</title>
<link rel="stylesheet" href="https://fonts.googleapis.com/css2?family=Montserrat:wght@400;600&family=Libre+Baskerville&display=swap">
<style>
  :root {
    --brand-blue: #1b6fc1;
    --text-dark: #2a2a2a;
    --page-bg: #ffffff;
    --band-text: #ffffff;
  }
  html, body {
    margin: 0;
    padding: 0;
    overflow: hidden;
    background: var(--page-bg);
  }
  .slide {
    position: relative;
    width: 1200px;
    height: 676px;
    overflow: hidden;
    background: var(--page-bg);
    font-family: "Montserrat", sans-serif;
    color: var(--text-dark);
  }
  .side-band {
    position: absolute;
    left: 0;
    top: 0;
    width: 44px;
    height: 100%;
    background: var(--brand-blue);
  }
  .side-band__url {
    position: absolute;
    left: 22px;
    top: 336px;
    transform: translate(-50%, -50%) rotate(-90deg);
    font-family: "Libre Baskerville", serif;
    font-size: 14px;
    color: var(--band-text);
    white-space: nowrap;
    letter-spacing: 0.2px;
  }
  .edge-band {
    position: absolute;
    right: 0;
    top: 0;
    width: 12px;
    height: 100%;
    background: var(--brand-blue);
  }
  .page-number {
    position: absolute;
    left: 1156px;
    top: 18px;
    font-family: "Libre Baskerville", serif;
    font-size: 18px;
    color: var(--text-dark);
  }
  .slide-title {
    position: absolute;
    left: 86px;
    top: 80px;
    margin: 0;
    font-size: 29px;
    font-weight: 600;
    color: var(--brand-blue);
    letter-spacing: 0.3px;
  }
  .point-list {
    position: absolute;
    left: 86px;
    top: 146px;
    margin: 0;
    padding: 0;
    list-style: none;
    font-size: 17.2px;
    line-height: 28px;
    letter-spacing: 0.3px;
  }
  .point-list li {
    position: relative;
    padding-left: 28px;
  }
  .point-list li::before {
    content: "";
    position: absolute;
    left: 4px;
    top: 10px;
    width: 6px;
    height: 6px;
    border: 2.5px solid var(--brand-blue);
    transform: rotate(45deg);
  }
  .point-list .sub-list {
    margin: 0;
    padding: 0 0 0 0;
    list-style: none;
    width: 560px;
  }
  .point-list .sub-list li {
    padding-left: 28px;
  }
  .emphasis {
    font-weight: 600;
    text-decoration: underline;
    text-underline-offset: 3px;
  }
  .coin-photo {
    position: absolute;
    left: 644px;
    top: 340px;
    width: 496px;
    height: 316px;
  }
  .brand-mark {
    position: absolute;
    left: 66px;
    top: 612px;
    display: flex;
    align-items: center;
    gap: 8px;
  }
  .brand-mark__dot {
    width: 30px;
    height: 30px;
    border-radius: 50%;
    background: var(--brand-blue);
  }
  .brand-mark__name {
    font-family: "Montserrat", sans-serif;
    font-size: 15px;
    font-weight: 600;
    color: var(--brand-blue);
    letter-spacing: 1.5px;
  }
</style>
</head>
<body>
<div class="slide">
  <div class="side-band">
    <span class="side-band__url">www.pinebrookcapital.com</span>
  </div>
  <div class="edge-band"></div>
  <div class="page-number">3</div>

  <h1 class="slide-title">WHEN IS A NON-CONTROL TRANSACTION APPROPRIATE?</h1>

  <ul class="point-list">
    <li>The company has opportunities to expand but requires capital to do so</li>
    <li>At least one active owner <span class="emphasis">is not</span> close to retirement</li>
    <li>The company is not in a turnaround situation</li>
    <li>Family members may work in the business and want to continue</li>
    <li>Owners care about keeping the business in their family name (legacy)</li>
    <li>Liquidity (dividend) is not the major use of the invested capital</li>
    <li>Owners are sensitive to utilizing too much debt</li>
    <li>Companies require more than just capital:
      <ul class="sub-list">
        <li>They may also need operational, marketing, financial, and/or technology counsel</li>
      </ul>
    </li>
  </ul>

  <svg class="coin-photo" role="img" aria-label="Photograph of stacked silver and copper coins" viewBox="0 0 496 316">
    <defs>
      <linearGradient id="coinTone" x1="0" y1="0" x2="1" y2="1">
        <stop offset="0" stop-color="#d9cbbd"/>
        <stop offset="0.5" stop-color="#a8876a"/>
        <stop offset="1" stop-color="#c98a55"/>
      </linearGradient>
    </defs>
    <rect width="496" height="316" rx="6" fill="url(#coinTone)"/>
  </svg>

  <div class="brand-mark">
    <span class="brand-mark__dot"></span>
    <span class="brand-mark__name">PINEBROOK CAPITAL</span>
  </div>
</div>
</body>
</html>
```